Label design for organic saffron, saffron and herbal syrup

We cultivate saffron, Damszen roses, flowers and herbs. We would need a recognizable outfit (label) for our products. Theoretically (and practically) we have "converted" the family coat of arms into a kind of LOGO. I would send this in the attachment. It would be nice if - in one way or another - this LOGO / coat of arms could be used (certainly with other colors). For some time we have played with the idea of changing the second part of the family name "Wallmoser" (in German .... greuth sounds similar to Kraut / herb [English]) .... eg Wallmoser's saffron syrup into the labeling.
Our products are primarily syrups, currently herbal syrup and saffron syrup. Here the first problem arises, the only bottles / caps that are actually approved for syrup filling (hot filling) are appallingly ugly (see attachment), the only possibility of "sprucing up" is to use so-called "shrink sleeves" (here we need a diameter of 31 and a length of about 40), the colors of which are also limited. Besides the syrup, we sell saffron as a spice and various herbal mixtures (see appendix current packaging saffron). Our quantities are small (syrup 200ml-330ml), saffron in the gram range.
We also need quasi the back of the labeling (this should be able to be redefined per charge) .... Batch 1 (with small quantity has eg more of herb xy than the next batch or the saffron syrup with batch xy needs more / less saffron). In addition, we are certified organic (for this reason, the reverse side would also have to contain all the requirements of organic labeling) [see attachment].
We do not really want to address a specific clientele. Maybe just people who want to taste, enjoy, mix drinks, cook .... (and - unfortunately - don't like Corvel syrup :-) and want to pay a bit more, or find our saffron or herbs better than others) .
In summary
- Strong recognition value (possibly inclusion of "coat of arms", color variable ... although I personally don't like yellow that much)
- Saffron syrup (the color of the saffron syrup is yellow / golden-yellow-light orange, in a transparent ugly bottle)
- Herbal syrup (color variable from blue / green / brown / red elements, in transparent ugly bottle)
Saffron and other herbs (very small containers, type of container not yet fixed)
Regarding a potential "style" I can unfortunately give little information. On the one hand, I am in love with minimalism, on the other hand, I find the translucent, cryptic, implied enormously attractive and sometimes even the "overloaded" colorful has its charm. I think that all in all, it just has to be coherent, and then it will be good.
Requirements
Must have
- Integration of Code of Arms, modifiable for different products

```html
<!DOCTYPE html>
<html lang="de">
<head>
<meta charset="utf-8">
<title>Wallmoser Rose Sirup – Etikett</title>
<link rel="stylesheet" href="https://fonts.googleapis.com/css2?family=Libre+Baskerville:wght@700&family=Pinyon+Script&family=Roboto+Condensed:wght@700&display=swap">
<style>
  :root {
    --maroon: #7d1a4e;
    --maroon-deep: #5e1139;
    --gold: #c9a24a;
    --gold-light: #ecd08a;
    --cream: #fdf3d3;
    --ink: #2a2330;
    --script-ink: #3b2c6e;
    --crest: #d9d2e4;
    --organic-light: #c6e09c;
    --organic-dark: #5f9a3a;
  }
  * { margin: 0; padding: 0; box-sizing: border-box; }
  html, body { width: 810px; height: 1200px; overflow: hidden; background: #ffffff; }
  .label {
    position: relative;
    width: 810px;
    height: 1200px;
    background: var(--cream);
    overflow: hidden;
    font-family: "Roboto Condensed", "Arial Narrow", sans-serif;
    font-weight: 700;
    color: var(--ink);
  }
  .header { position: absolute; left: 0; top: 0; }
  .brand-name {
    position: absolute;
    left: 0; width: 810px; top: 318px;
    text-align: center;
    font-family: "Pinyon Script", cursive;
    font-weight: 400;
    font-size: 66px;
    color: var(--script-ink);
    line-height: 1;
  }
  .product-shield { position: absolute; left: 232px; top: 448px; }
  .product-title {
    position: absolute;
    left: 232px; width: 348px; top: 578px;
    text-align: center;
    font-family: "Libre Baskerville", Georgia, serif;
    font-weight: 700;
    font-size: 82px;
    line-height: 86px;
    color: #ffffff;
    text-shadow:
      -3px -3px 0 var(--ink), 3px -3px 0 var(--ink),
      -3px 3px 0 var(--ink), 3px 3px 0 var(--ink),
      0 3px 0 var(--ink), 0 -3px 0 var(--ink),
      3px 0 0 var(--ink), -3px 0 0 var(--ink),
      5px 6px 4px rgba(0,0,0,0.45);
  }
  .producer-info {
    position: absolute;
    left: 672px; top: 520px;
    height: 392px;
    writing-mode: vertical-rl;
    transform: rotate(180deg);
    font-weight: 700;
    font-size: 18px;
    line-height: 22px;
    letter-spacing: 0.6px;
    color: var(--ink);
  }
  .best-before {
    position: absolute;
    left: 679px; top: 932px;
    width: 74px; height: 162px;
    background: #ffffff;
    border: 2px solid var(--ink);
  }
  .best-before span {
    position: absolute;
    left: 6px; bottom: 8px;
    writing-mode: vertical-rl;
    transform: rotate(180deg);
    font-weight: 700;
    font-size: 17px;
  }
  .volume, .dilution {
    position: absolute;
    top: 1108px;
    font-family: "Roboto Condensed", "Arial Narrow", sans-serif;
    font-weight: 700;
    font-size: 21px;
    color: var(--ink);
  }
  .volume { left: 290px; }
  .dilution { left: 472px; }
  .organic-badges { position: absolute; left: 372px; top: 980px; }
</style>
</head>
<body>
<main class="label">
  <svg class="header" width="810" height="460" viewBox="0 0 810 460">
    <defs>
      <linearGradient id="band-tone" x1="0" y1="0" x2="1" y2="1">
        <stop offset="0" stop-color="#8a2258"/>
        <stop offset="0.5" stop-color="#7d1a4e"/>
        <stop offset="1" stop-color="#6a1442"/>
      </linearGradient>
      <linearGradient id="gold-band" x1="0" y1="0" x2="0" y2="1">
        <stop offset="0" stop-color="#a8822f"/>
        <stop offset="0.45" stop-color="#ecd08a"/>
        <stop offset="1" stop-color="#a8822f"/>
      </linearGradient>
    </defs>
    <rect class="header-ornament" x="0" y="0" width="810" height="433" fill="url(#band-tone)"
          role="img" aria-label="Gold paisley and floral lace ornament on deep rose background"/>
    <path class="header-window" d="M274 0 H538 V100 A237 237 0 0 1 600 433 H212 A237 237 0 0 1 274 100 Z"
          fill="#ffffff" stroke="var(--gold)" stroke-width="3"/>
    <circle class="crest-mark" cx="406" cy="232" r="58" fill="var(--crest)"/>
    <rect class="gold-band" x="0" y="426" width="810" height="22" fill="url(#gold-band)"/>
  </svg>
  <div class="brand-name">Wallmoser</div>

  <svg class="product-shield" width="348" height="492" viewBox="0 0 348 492"
       role="img" aria-label="Faint line drawing of a rose with stem and leaves">
    <defs>
      <linearGradient id="shield-tone" x1="0" y1="0" x2="0" y2="1">
        <stop offset="0" stop-color="#7d1a4e"/>
        <stop offset="1" stop-color="#86265a"/>
      </linearGradient>
    </defs>
    <path d="M0 0 H348 V318 A174 174 0 0 1 0 318 Z" fill="url(#shield-tone)"/>
  </svg>
  <h1 class="product-title">Rose<br>Sirup</h1>

  <p class="producer-info">
    *aus kontrolliert biologischer Landwirtschaft<br>
    Expertly crafted by: Halden-Wallmoser<br>
    Lindenweg 4, 8300 Feldau
  </p>

  <div class="best-before"><span>Best Before:</span></div>

  <span class="volume">330mL</span>
  <svg class="organic-badges" width="72" height="156" viewBox="0 0 72 156">
    <rect x="0" y="0" width="72" height="156" fill="var(--organic-light)"/>
    <circle cx="36" cy="30" r="20" fill="var(--organic-dark)"/>
    <rect x="10" y="66" width="52" height="40" fill="var(--organic-dark)"/>
    <rect x="10" y="116" width="52" height="10" fill="var(--organic-dark)" opacity="0.5"/>
  </svg>
  <span class="dilution">1:7</span>
</main>
</body>
</html>
```